BOLD & MINIMALIST DESIGN NEEDED

We want a very bold but minimalistic business card design that is impactful and utilizes both sides of the business card. Our current logo is included for your use.

We want bold fonts and good use of negative space. We don't want the logo to overpower the design.

Target Market(s)

Professionals who are building new commercial buildings.

Industry/Entity Type

Construction

Contact Information for Business Card

Name, Title, email, office phone, cell phone, website

Font styles to use
Serif
Sans Serif

Requirements
Must have
• Bold design!

```html
<!DOCTYPE html>
<html lang="en">
<head>
<meta charset="utf-8">
<title>Ridgeway Build Co — Business Card</title>
<link href="https://fonts.googleapis.com/css2?family=Lato:wght@400;700;900&display=swap" rel="stylesheet">
<style>
  :root {
    --stage: #2a2a2a;
    --green: #6aa51f;
    --green-light: #86c232;
    --green-dark: #2f5710;
    --green-mid: #4f7f19;
    --ink: #1a1a1a;
    --paper: #ffffff;
    --muted: #333333;
  }
  * { box-sizing: border-box; margin: 0; padding: 0; }
  html, body { width: 1200px; height: 800px; overflow: hidden; }
  body {
    background: var(--stage);
    font-family: "Lato", Arial, sans-serif;
    position: relative;
  }
  .card {
    position: absolute;
    width: 600px;
    height: 340px;
    border-radius: 16px;
    overflow: hidden;
  }

  /* Front side */
  .card-front {
    left: 110px;
    top: 45px;
    background: radial-gradient(circle at 35% 30%, var(--green-mid) 0%, #467316 45%, var(--green-dark) 100%);
  }
  .card-front .brand {
    position: absolute;
    left: 48px;
    top: 150px;
    width: 270px;
    display: flex;
    align-items: center;
    gap: 12px;
    color: var(--paper);
    font-weight: 900;
    font-size: 30px;
    line-height: 1.1;
    letter-spacing: 0.5px;
    text-transform: uppercase;
  }
  .brand-mark {
    width: 22px;
    height: 22px;
    background: var(--green-light);
    flex: none;
  }
  .card-front .emblem-area {
    position: absolute;
    right: 0;
    top: 0;
    width: 250px;
    height: 100%;
    background: linear-gradient(135deg, #0d0d0d 0%, #1c1c1c 40%, var(--green-light) 41%, #9bd24a 70%, #3c6b12 100%);
  }

  /* Back side */
  .card-back {
    left: 490px;
    top: 410px;
    background: var(--paper);
  }
  .card-back .tab {
    position: absolute;
    right: 0;
    top: 30px;
    width: 26px;
    height: 34px;
    background: var(--green);
  }
  .card-back .person {
    position: absolute;
    right: 40px;
    top: 28px;
    text-align: right;
  }
  .person .name {
    color: var(--green);
    font-weight: 900;
    font-size: 30px;
    line-height: 1.05;
  }
  .person .title {
    color: var(--muted);
    font-size: 15px;
    margin-top: 2px;
  }
  .card-back .brand {
    position: absolute;
    left: 40px;
    top: 128px;
    display: flex;
    align-items: center;
    gap: 10px;
    color: var(--ink);
    font-weight: 900;
    font-size: 28px;
    text-transform: uppercase;
  }
  .card-back .brand .brand-mark { background: var(--green); width: 18px; height: 18px; }
  .rule {
    position: absolute;
    left: 0;
    right: 0;
    top: 214px;
    height: 2px;
    background: var(--green);
  }
  .band {
    position: absolute;
    left: 0;
    right: 0;
    bottom: 0;
    height: 120px;
    background: linear-gradient(180deg, var(--green-light), var(--green));
    color: var(--paper);
    display: flex;
    justify-content: space-between;
    padding: 20px 40px;
    font-size: 16px;
  }
  .contact-list { list-style: none; }
  .contact-list li {
    display: flex;
    align-items: center;
    gap: 8px;
    line-height: 26px;
  }
  .contact-list svg { width: 14px; height: 14px; fill: var(--paper); flex: none; }
  .location { text-align: right; line-height: 22px; }
  .location .web {
    display: flex;
    justify-content: flex-end;
    align-items: center;
    gap: 8px;
    margin-top: 12px;
  }
  .location svg { width: 14px; height: 14px; }
</style>
</head>
<body>

  <section class="card card-front" aria-label="Business card front">
    <div class="brand"><span class="brand-mark"></span><span>Ridgeway<br>Build Co</span></div>
    <div class="emblem-area" role="img" aria-label="Large dimensional company emblem decoration"></div>
  </section>

  <section class="card card-back" aria-label="Business card back">
    <div class="tab"></div>
    <div class="person">
      <div class="name">Daniel Carter</div>
      <div class="title">Founder &amp; CEO</div>
    </div>
    <div class="brand"><span class="brand-mark"></span>Ridgeway Build Co</div>
    <div class="rule"></div>
    <div class="band">
      <ul class="contact-list">
        <li>
          <svg viewBox="0 0 24 24"><path d="M6.6 10.8a15.1 15.1 0 0 0 6.6 6.6l2.2-2.2a1 1 0 0 1 1-.25 11.4 11.4 0 0 0 3.6.6 1 1 0 0 1 1 1V20a1 1 0 0 1-1 1A17 17 0 0 1 3 4a1 1 0 0 1 1-1h3.5a1 1 0 0 1 1 1c0 1.25.2 2.45.6 3.6a1 1 0 0 1-.25 1z"/></svg>
          555-210-4471
        </li>
        <li>
          <svg viewBox="0 0 24 24"><rect x="6" y="2" width="12" height="20" rx="2"/><rect x="8" y="4" width="8" height="13" fill="#86c232"/></svg>
          555-388-9025
        </li>
        <li>
          <svg viewBox="0 0 24 24"><path d="M2 12 22 3l-6 19-4-8z"/></svg>
          hello@ridgewaybuild.com
        </li>
      </ul>
      <div class="location">
        <div>4820 Harbor Point Blvd 210-B,</div>
        <div>FL 32401</div>
        <div class="web">
          <svg viewBox="0 0 24 24" fill="none" stroke="#ffffff" stroke-width="2"><circle cx="12" cy="12" r="9"/><path d="M3 12h18M12 3c3 3 3 15 0 18M12 3c-3 3-3 15 0 18"/></svg>
          www.ridgewaybuild.com
        </div>
      </div>
    </div>
  </section>

</body>
</html>
```